Book Title: “Faith: Road of Endless Grace” Please see the attachment “Text on the cover”.

Book Cover Design Instructions: This book is meant for people of all religions and nationalities. Therefore, on the cover, there should be no mosque or an object specific to any religion. The primary emphasis should be on the "unconditional love of God." Therefore, use universal symbols of love. The second priority themes could be Sufism, Peace, and self-improvement. Rest is your imagination. Please also see the attachment: 'Book description and author's Bio.'
This book has the potential to be a best seller. Please do a good job.
What Book Cover Formats are required: A designer should submit cover designs in three formats: (1) eBook, (2) Paperback, and (3) Hardback. These books will be published on Borvex QPL.
Format requirements for eBooks are available from: https://qpl.borvex.example/en_US/help/topic/R731928457.
You can find paperback and hardback cover measurements from: https://qpl.borvex.example/en_US/cover-calculator
• To complete the project, all three formats should be accepted by Borvex QPL.
• The book interior trim size is 6.14 X 9.21 inches.
• Interior Type: Premium color.
• No bleed.
• I do not upload barcode. So, the back cover should have room for Borvex to print the barcode.
• Number of pages 126.
Compensation for the designer: After selecting one designer, I will increase the amount by $200 on Artvelle to compensate for three deliverables.
Follow-up of the Project:
After the book is published, I may need minor revisions. For example, the number of pages may change. Therefore, I will need the same design in revised sizes. In that case, I will pay $25 for each revision. For example, if the number of pages changes, I will need a different spine for paperback and hardback, then I will pay the artist $25 + $25 = $50 for both designs.
List of Enclosers:
1. Text on the cover.
2. Book description and author's Bio for the back cover.
3. Later, I will upload my picture for the book's back cover.

Target Market(s)

Any adult

Industry/Entity Type

Any industry

Requirements
Must have
• Three Deliverables

```html
<!DOCTYPE html>
<html lang="en">
<head>
<meta charset="utf-8">
<title>Faith: Road of Endless Grace — Cover</title>
<link rel="stylesheet" href="https://fonts.googleapis.com/css2?family=Bebas+Neue&family=Montserrat:wght@500;600&display=swap">
<style>
  :root {
    --orange-deep: #d85a1b;
    --orange-mid: #e8751f;
    --orange-warm: #f39a2c;
    --amber: #f7b23a;
    --sun: #fff4c8;
    --ink: #111111;
    --paper: #ffffff;
  }
  html, body {
    margin: 0;
    padding: 0;
    width: 800px;
    height: 1200px;
    overflow: hidden;
    background: var(--orange-deep);
  }
  .cover {
    position: relative;
    width: 800px;
    height: 1200px;
    overflow: hidden;
    background: linear-gradient(180deg, var(--orange-deep) 0%, var(--orange-mid) 45%, var(--orange-warm) 68%, var(--amber) 100%);
  }
  .cover-art {
    position: absolute;
    left: 0;
    top: 800px;
    width: 800px;
    height: 400px;
    background:
      radial-gradient(ellipse 180px 160px at 392px 150px, var(--sun) 0%, rgba(255,240,180,0.85) 35%, rgba(250,190,70,0) 100%),
      radial-gradient(ellipse 300px 140px at 400px 330px, rgba(255,236,150,0.9) 0%, rgba(255,200,80,0) 100%),
      linear-gradient(180deg, rgba(243,154,44,0) 0%, rgba(196,96,24,0.55) 55%, rgba(150,60,15,0.6) 100%);
  }
  .title-art {
    position: absolute;
    left: 0;
    top: 0;
    width: 800px;
    height: 1200px;
  }
  .kicker, .title-line {
    fill: var(--paper);
  }
  .kicker {
    font-family: "Montserrat", sans-serif;
    font-weight: 500;
    font-size: 37px;
  }
  .title-line {
    font-family: "Bebas Neue", sans-serif;
  }
  .subtitle {
    position: absolute;
    left: 0;
    width: 800px;
    top: 722px;
    margin: 0;
    text-align: center;
    font-family: "Montserrat", sans-serif;
    font-weight: 500;
    font-size: 37px;
    line-height: 43px;
    letter-spacing: 0.5px;
    color: var(--ink);
  }
  .author {
    position: absolute;
    left: 0;
    width: 800px;
    top: 1147px;
    margin: 0;
    text-align: center;
    font-family: "Montserrat", sans-serif;
    font-weight: 600;
    font-size: 40px;
    line-height: 48px;
    letter-spacing: 2px;
    color: var(--ink);
  }
</style>
</head>
<body>
  <main class="cover">
    <div class="cover-art" role="img" aria-label="Sunset photograph of two hands forming a heart shape against a glowing sun"></div>

    <svg class="title-art" viewBox="0 0 800 1200" width="800" height="1200" aria-label="Unconditional Love of God — Faith: Road of Endless Grace">
      <text class="kicker" x="400" y="48" text-anchor="middle" textLength="587" lengthAdjust="spacingAndGlyphs">UNCONDITIONAL LOVE OF GOD</text>
      <text class="title-line" x="53" y="324" font-size="377" textLength="694" lengthAdjust="spacingAndGlyphs">FAITH</text>
      <text class="title-line" x="55" y="551" font-size="282" textLength="690" lengthAdjust="spacingAndGlyphs">ROAD OF</text>
      <text class="title-line" x="51" y="696" font-size="165" textLength="693" lengthAdjust="spacingAndGlyphs">ENDLESS GRACE</text>
    </svg>

    <p class="subtitle">GUIDE TO CULTIVATING INNER<br>PEACE AND MINDFUL LIVING</p>
    <p class="author">DR. REYHAN ALVANI</p>
  </main>
</body>
</html>
```